Merry Perch Wild Bird Food Gusset Bag Deisgn

We’re looking to transition from our current packaging—using a sticker on a bag—to a fully printed film design. The goal is to modernize the look and make it more fun while staying true to our existing brand identity.
We’d like to retain the same color scheme, fonts, and artwork style currently used on our bags. The barcode and product information should be placed on the back of the bag.
Bag specifications:
Dimensions: 410mm (length) x 530mm (width)
Design: Predominantly white with strategically placed transparent areas to allow the product to be seen inside.
There are 10 different bag designs required for this range.
We have attached our current labels of each product there is a Circle one and also a rectangle one that all all product information
We would also likes explained and also a image showing the these 5L bags refill 5L Tubs
We’ll also attach some example bags that represent the look and feel we’re aiming for in the new designs.
The bag is a gusset bag, Icon attached as an example
Target Market(s)
Wild Bird Food Buyers
Look and feel

```html
<!DOCTYPE html>
<html lang="en">
<head>
<meta charset="utf-8">
<title>Merry Perch Wild Bird Food Range</title>
<link rel="stylesheet" href="https://fonts.googleapis.com/css2?family=Chewy&family=Nunito:wght@400;800&display=swap">
<style>
  :root {
    --stage: #d6d6d8;
    --paper: #f1efe9;
    --paper-shade: #e4e1d9;
    --brand: #1c9a89;
    --grass-top: #a6d46a;
    --grass-bottom: #4f9a2c;
    --ink: #222222;
  }
  * { box-sizing: border-box; margin: 0; padding: 0; }
  html, body { width: 1200px; height: 2984px; overflow: hidden; }
  body {
    background: var(--stage);
    font-family: 'Nunito', sans-serif;
  }
  .range {
    display: grid;
    grid-template-columns: 350px 350px;
    grid-auto-rows: 530px;
    column-gap: 190px;
    row-gap: 35px;
    padding: 65px 0 0 195px;
  }
  .bag {
    display: flex;
    width: 350px;
    height: 530px;
    box-shadow: 0 14px 24px rgba(0,0,0,.18);
  }
  .bag__gusset {
    width: 42px;
    background: var(--side);
    padding: 150px 5px 0;
    font-size: 6px;
    line-height: 1.5;
    color: rgba(255,255,255,.75);
  }
  .bag__front {
    position: relative;
    flex: 1;
    background: linear-gradient(180deg, var(--paper), var(--paper-shade));
    display: flex;
    flex-direction: column;
    align-items: center;
    overflow: hidden;
  }
  .brand {
    display: flex;
    align-items: center;
    gap: 6px;
    margin-top: 30px;
    font-weight: 800;
    font-size: 15px;
    color: var(--brand);
  }
  .brand__dot {
    width: 14px; height: 14px; border-radius: 50%;
    background: var(--brand);
  }
  .bag__title {
    font-family: 'Chewy', cursive;
    font-weight: 400;
    font-size: 44px;
    line-height: 1;
    text-align: center;
    color: var(--title);
    margin-top: 14px;
    height: 92px;
    display: flex;
    align-items: center;
  }
  .bag__scene {
    width: 260px;
    height: 140px;
    margin-top: 6px;
    border-radius: 40% 40% 10px 10px;
    background: radial-gradient(ellipse at 50% 60%, var(--scene-a), var(--scene-b) 70%, transparent 72%);
  }
  .bag__window {
    width: 100%;
    height: 150px;
    margin-top: 2px;
    background: linear-gradient(160deg, var(--fill-a), var(--fill-b));
    border-top: 4px solid #fff;
  }
  .bag__grass {
    position: absolute;
    left: 0; right: 0; bottom: 0;
    height: 52px;
    background: linear-gradient(180deg, var(--grass-top), var(--grass-bottom));
  }
  .bag__weight {
    position: absolute;
    right: 14px;
    bottom: 58px;
    font-weight: 800;
    font-size: 16px;
    color: var(--ink);
  }
</style>
</head>
<body>
<main class="range">

  <article class="bag" style="--side:#6aa832;--title:#1e1e1e;--scene-a:#e8b632;--scene-b:#7aa05a;--fill-a:#7c7f86;--fill-b:#3f4248">
    <div class="bag__gusset"><p>Fresh food for garden birds. Store cool and dry.</p></div>
    <div class="bag__front">
      <div class="brand"><span class="brand__dot"></span>Merry Perch</div>
      <h2 class="bag__title">Black<br>Sunflower</h2>
      <div class="bag__scene" role="img" aria-label="Illustration of a tit on stones among sunflowers"></div>
      <div class="bag__window" role="img" aria-label="Window showing black sunflower seeds"></div>
      <div class="bag__grass" role="img" aria-label="Grass border"></div>
      <span class="bag__weight">5lbs</span>
    </div>
  </article>

  <article class="bag" style="--side:#8b6a4a;--title:#8a6a45;--scene-a:#8a8f96;--scene-b:#6fae4a;--fill-a:#b8945a;--fill-b:#7d5f34">
    <div class="bag__gusset"><p>Fresh food for garden birds. Store cool and dry.</p></div>
    <div class="bag__front">
      <div class="brand"><span class="brand__dot"></span>Merry Perch</div>
      <h2 class="bag__title">Calci<br>Worms</h2>
      <div class="bag__scene" role="img" aria-label="Illustration of three birds on rocks with flowers"></div>
      <div class="bag__window" role="img" aria-label="Window showing calci worms"></div>
      <div class="bag__grass" role="img" aria-label="Grass border"></div>
      <span class="bag__weight">5lbs</span>
    </div>
  </article>

  <article class="bag" style="--side:#7a3a1f;--title:#8a4020;--scene-a:#d7a065;--scene-b:#8a7a66;--fill-a:#c7864a;--fill-b:#7a4a22">
    <div class="bag__gusset"><p>Fresh food for garden birds. Store cool and dry.</p></div>
    <div class="bag__front">
      <div class="brand"><span class="brand__dot"></span>Merry Perch</div>
      <h2 class="bag__title">Dried<br>Mealworms</h2>
      <div class="bag__scene" role="img" aria-label="Illustration of a robin on a log with mealworms"></div>
      <div class="bag__window" role="img" aria-label="Window showing dried mealworms"></div>
      <div class="bag__grass" role="img" aria-label="Grass border"></div>
      <span class="bag__weight">5lbs</span>
    </div>
  </article>

  <article class="bag" style="--side:#151515;--title:#1a1a1a;--scene-a:#e6a42a;--scene-b:#5e8c44;--fill-a:#3a3430;--fill-b:#151210">
    <div class="bag__gusset"><p>Fresh food for garden birds. Store cool and dry.</p></div>
    <div class="bag__front">
      <div class="brand"><span class="brand__dot"></span>Merry Perch</div>
      <h2 class="bag__title">Niger<br>Seed</h2>
      <div class="bag__scene" role="img" aria-label="Illustration of a finch with yellow flowers and rocks"></div>
      <div class="bag__window" role="img" aria-label="Window showing niger seed"></div>
      <div class="bag__grass" role="img" aria-label="Grass border"></div>
      <span class="bag__weight">5lbs</span>
    </div>
  </article>

  <article class="bag" style="--side:#3aaed0;--title:#3aaed0;--scene-a:#6aa848;--scene-b:#2f6e34;--fill-a:#b59a78;--fill-b:#6e5a44">
    <div class="bag__gusset"><p>Fresh food for garden birds. Store cool and dry.</p></div>
    <div class="bag__front">
      <div class="brand"><span class="brand__dot"></span>Merry Perch</div>
      <h2 class="bag__title">No Mess<br>Mix</h2>
      <div class="bag__scene" role="img" aria-label="Illustration of a kingfisher in a leafy garden"></div>
      <div class="bag__window" role="img" aria-label="Window showing no mess seed mix"></div>
      <div class="bag__grass" role="img" aria-label="Grass border"></div>
      <span class="bag__weight">5lbs</span>
    </div>
  </article>

  <article class="bag" style="--side:#8a7f76;--title:#7b7068;--scene-a:#b9905e;--scene-b:#4f8a3c;--fill-a:#efdcbc;--fill-b:#c9a880">
    <div class="bag__gusset"><p>Fresh food for garden birds. Store cool and dry.</p></div>
    <div class="bag__front">
      <div class="brand"><span class="brand__dot"></span>Merry Perch</div>
      <h2 class="bag__title">Peanut<br>Granules</h2>
      <div class="bag__scene" role="img" aria-label="Illustration of a garden feeding station with peanuts"></div>
      <div class="bag__window" role="img" aria-label="Window showing peanut granules"></div>
      <div class="bag__grass" role="img" aria-label="Grass border"></div>
      <span class="bag__weight">5lbs</span>
    </div>
  </article>

  <article class="bag" style="--side:#a8692c;--title:#c0772e;--scene-a:#d9a35a;--scene-b:#5e9a44;--fill-a:#ecdcc0;--fill-b:#c9ad86">
    <div class="bag__gusset"><p>Fresh food for garden birds. Store cool and dry.</p></div>
    <div class="bag__front">
      <div class="brand"><span class="brand__dot"></span>Merry Perch</div>
      <h2 class="bag__title">Peanuts<br>In Shell</h2>
      <div class="bag__scene" role="img" aria-label="Illustration of a bird on a stump with flowers and peanuts"></div>
      <div class="bag__window" role="img" aria-label="Window showing peanuts in shell"></div>
      <div class="bag__grass" role="img" aria-label="Grass border"></div>
      <span class="bag__weight">5lbs</span>
    </div>
  </article>

  <article class="bag" style="--side:#a88a3a;--title:#a9873e;--scene-a:#a8744a;--scene-b:#4f8a3c;--fill-a:#c08a66;--fill-b:#8a5a40">
    <div class="bag__gusset"><p>Fresh food for garden birds. Store cool and dry.</p></div>
    <div class="bag__front">
      <div class="brand"><span class="brand__dot"></span>Merry Perch</div>
      <h2 class="bag__title">Peanuts</h2>
      <div class="bag__scene" role="img" aria-label="Illustration of a birdhouse with red flowers and peanuts"></div>
      <div class="bag__window" role="img" aria-label="Window showing red-skinned peanuts"></div>
      <div class="bag__grass" role="img" aria-label="Grass border"></div>
      <span class="bag__weight">5lbs</span>
    </div>
  </article>

  <article class="bag" style="--side:#e0a21f;--title:#e8a530;--scene-a:#f0b62a;--scene-b:#4f9a3c;--fill-a:#d6d2c8;--fill-b:#a8a298">
    <div class="bag__gusset"><p>Fresh food for garden birds. Store cool and dry.</p></div>
    <div class="bag__front">
      <div class="brand"><span class="brand__dot"></span>Merry Perch</div>
      <h2 class="bag__title">Sunflower<br>Hearts</h2>
      <div class="bag__scene" role="img" aria-label="Illustration of sunflowers, a tree and a birdhouse"></div>
      <div class="bag__window" role="img" aria-label="Window showing sunflower hearts"></div>
      <div class="bag__grass" role="img" aria-label="Grass border"></div>
      <span class="bag__weight">5lbs</span>
    </div>
  </article>

  <article class="bag" style="--side:#1f6b2e;--title:#1f6b2e;--scene-a:#c7a77a;--scene-b:#7aa25a;--fill-a:#b8a68a;--fill-b:#5e5246">
    <div class="bag__gusset"><p>Fresh food for garden birds. Store cool and dry.</p></div>
    <div class="bag__front">
      <div class="brand"><span class="brand__dot"></span>Merry Perch</div>
      <h2 class="bag__title">Wild<br>Bird Mix</h2>
      <div class="bag__scene" role="img" aria-label="Illustration of small birds among wild grasses and seed"></div>
      <div class="bag__window" role="img" aria-label="Window showing wild bird seed mix"></div>
      <div class="bag__grass" role="img" aria-label="Grass border"></div>
      <span class="bag__weight">5lbs</span>
    </div>
  </article>

</main>
</body>
</html>
```